Wedding Invitation for a wedding at home - personal, romantic event

Want a wedding invitation that is to be printed onto card.
Size to be 148mm x 210mm
For it to open like a book not tent card
Have a picture of a house that I want to be the front cover.
I've attached 2 pictures. I like the picture without the man but with the grass
For the photo to become a drawing and the colours to be brighter.
If you could use the picture of us and get us in one of the windows.
If you could put the picture of the dog maybe somewhere on the grass.
Love the colour of the sky in the picture of the beach

Words to be on the inside of the card:
Together with our families
You are invited to the Wedding Reception of Tessa Pimble and Roy Fenwick
On Saturday 9th of September 2017 at 6pm
At Fenwick's Keep, 41b, Marrow Crescent, Camberley, Surrey, RH19 4PW
Carriages at 1am
RSVP by Friday 27th of July to 07713 586 201

Words on the Back page:
With all that we have, we've been truly blessed.
Your presence and prayers are all that we request.
But if you desire to give nonetheless,
Monetary gift is one we suggest.

If the pages can be white.
Writing in gold
gold border on all pages

Target Market(s)

Wedding guests

Industry/Entity Type

Wedding

Font styles to use
Script

Requirements
Must have
• Romantic feel. Our wedding colours are white, gold and rose gold.
• Designer to be creative and I do not have much inspiration.
Nice to have
• metallic colours
• Maybe have MR & MRS in gold metallic on the front page

```html
<!DOCTYPE html>
<html lang="en">
<head>
<meta charset="utf-8">
<title>Wedding Reception Invitation – Tessa Pimble &amp; Roy Fenwick</title>
<link rel="stylesheet" href="https://fonts.googleapis.com/css2?family=EB+Garamond:wght@400&family=Great+Vibes&display=swap">
<style>
  :root {
    --paper: #ffffff;
    --ink: #111111;
  }
  html, body {
    margin: 0;
    padding: 0;
    overflow: hidden;
    background: var(--paper);
  }
  .invitation {
    position: relative;
    width: 846px;
    height: 1200px;
    background: var(--paper);
    color: var(--ink);
    overflow: hidden;
  }
  .line {
    position: absolute;
    left: 0;
    width: 100%;
    margin: 0;
    text-align: center;
    font-family: "EB Garamond", "Times New Roman", serif;
    font-size: 26px;
    line-height: 32px;
    letter-spacing: 0.8px;
    text-transform: uppercase;
    white-space: nowrap;
  }
  .line--and {
    font-size: 29px;
    letter-spacing: 0;
  }
  .couple-name {
    position: absolute;
    left: 0;
    width: 100%;
    margin: 0;
    text-align: center;
    font-family: "Great Vibes", cursive;
    font-weight: 400;
    font-size: 88px;
    line-height: 100px;
    white-space: nowrap;
  }
</style>
</head>
<body>
  <main class="invitation">
    <p class="line" style="top:204px;">Together with our families</p>

    <h1 class="couple-name" style="top:254px;">Tessa Pimble</h1>
    <p class="line line--and" style="top:374px;">and</p>
    <h1 class="couple-name" style="top:410px;">Roy Fenwick</h1>

    <p class="line" style="top:554px;">Invite you to their</p>
    <p class="line" style="top:586px;">Wedding Reception</p>

    <p class="line" style="top:650px;">On Saturday 9th of September 2017</p>
    <p class="line" style="top:682px;">at 6pm</p>

    <p class="line" style="top:746px;">At Fenwick’s Keep</p>
    <p class="line" style="top:778px;">41b, Marrow Crescent, Camberley</p>
    <p class="line" style="top:810px;">Surrey, RH19 4PW</p>

    <p class="line" style="top:874px;">Carriages at 1am</p>

    <p class="line" style="top:1005px;">RSVP by Friday 27th of July</p>
    <p class="line" style="top:1038px;">to 07713 586 201</p>
  </main>
</body>
</html>
```